Refresh Application User Interface

Brightmoor wishes to update the look of its business applications. Two representative forms are shown below. Please note, we are not considering changes in functionality or usability. Our goal is a cleaner, more contemporary design.

Industry/Entity Type

Business

```html
<!DOCTYPE html>
<html lang="en">
<head>
<meta charset="utf-8">
<title>Brightmoor – Purchase Order Lines</title>
<link rel="stylesheet" href="https://fonts.googleapis.com/css2?family=Inter:wght@400;500;600;700&display=swap">
<style>
:root{
  --app-bg:#1c2027;
  --topbar:#111419;
  --tab:#2a3039;
  --tab-hover:#343b46;
  --green:#6bbf3f;
  --green-deep:#4a9a22;
  --blue:#3d6fa8;
  --blue-soft:#5a8cc4;
  --brand:#5aa2f0;
  --surface:#ffffff;
  --panel:#f5f7fa;
  --line:#e1e6ec;
  --field:#eef1f5;
  --field-border:#d3dae3;
  --text:#1f2630;
  --muted:#5c6673;
  --select-text:#1f3a6e;
  --ok:#2f8f3a;
  --link:#2f5fd6;
  --status:#fbf8e6;
  --status-line:#ece2ad;
  --lock:#f0d96a;
}
*{box-sizing:border-box;margin:0;padding:0}
html,body{width:1200px;height:897px;overflow:hidden;background:var(--app-bg)}
body{position:relative;font-family:"Inter",Arial,sans-serif;color:var(--text);font-size:14px}
.abs{position:absolute}

/* top bar */
.topbar{left:0;top:0;width:1200px;height:31px;background:var(--topbar);color:#e9edf2;font-size:13.5px;display:flex;align-items:center}
.topbar b{font-weight:600;color:#fff}
.session{display:flex;gap:34px;padding-left:21px;align-items:center}
.session span{display:flex;align-items:center;gap:6px}
.utility{margin-left:auto;display:flex;height:31px}
.utility span{display:flex;align-items:center;padding:0 11px;border-left:1px solid #2b3038}
.utility span:first-child{border-left:none}

/* modules */
.modules{left:22px;top:45px;display:flex;gap:3px}
.modules span{height:32px;padding:0 13px;display:flex;align-items:center;background:var(--tab);color:#eef2f6;font-size:15.5px;font-weight:500;border-radius:6px 6px 0 0}
.modules .active{background:var(--green);color:#fff}
.brand{left:958px;top:40px;font-size:30px;font-weight:700;color:var(--brand);letter-spacing:.5px}

/* sub navigation */
.subnav{left:0;top:77px;width:1200px;height:31px;background:var(--green);display:flex;align-items:center;padding-left:22px;gap:0}
.subnav span{color:#fff;font-size:14px;font-weight:500;padding:0 8px;white-space:nowrap}
.subnav .active{background:#fff;color:var(--green-deep);border-radius:5px;padding:3px 8px;font-weight:600;margin-right:8px}
.subnav .divider{width:1px;height:16px;background:rgba(255,255,255,.55);padding:0;margin:0 8px}

/* title row */
.page-title{left:21px;top:121px;font-size:23px;font-weight:600;color:#fff;letter-spacing:-.2px}
.view-tabs{left:893px;top:124px;display:flex;gap:2px}
.view-tabs span{position:relative;height:30px;padding:0 10px;display:flex;align-items:center;color:#eef2f6;font-size:15px;border-radius:6px 6px 0 0}
.view-tabs .active{background:var(--blue);color:#fff}
.view-tabs .dot::after{content:"";position:absolute;right:1px;top:2px;width:7px;height:7px;border-radius:50%;background:var(--green)}

/* toolbar */
.toolbar{left:22px;top:154px;width:1158px;height:32px;background:var(--blue);border-radius:6px 6px 0 0;display:flex;align-items:center;color:#fff;font-size:14px}
.tool{display:flex;align-items:center;gap:7px;height:32px;padding:0 10px;border-right:1px solid rgba(255,255,255,.18)}
.tool.left-sep{border-left:1px solid rgba(255,255,255,.18)}
.tool.last{border-right:none}
.tool.dim{opacity:.5}
.spacer{flex:1}

/* content */
.content{left:22px;top:186px;width:1158px;height:683px;background:var(--surface);border-radius:0 0 6px 6px}
.panel{left:34px;top:198px;width:1133px;height:617px;background:var(--panel);border:1px solid var(--line);border-radius:8px}

.row{position:absolute;display:flex;align-items:center;height:24px}
.label{display:inline-block;text-align:right;color:var(--text);font-size:14px;white-space:nowrap}
.field{height:24px;background:var(--field);border:1px solid var(--field-border);border-radius:5px;padding:0 7px;display:flex;align-items:center;font-size:14px;color:var(--text)}
.select{position:relative;height:22px;background:#fff;border:1px solid #b9c3cf;border-radius:5px;padding:0 26px 0 6px;display:flex;align-items:center;font-size:14px;color:var(--select-text)}
.select i{position:absolute;right:0;top:0;width:22px;height:100%;border-left:1px solid var(--line)}
.select i::after{content:"";position:absolute;left:7px;top:5px;width:6px;height:6px;border-right:1.6px solid #4a5563;border-bottom:1.6px solid #4a5563;transform:rotate(45deg)}
.req{color:#8a94a1;font-size:15px;align-self:flex-start;margin-left:3px;margin-top:-4px}
.order-type{color:var(--ok);font-size:15.5px}
.hold{color:var(--link);font-size:15.5px}
.dpv{color:var(--link);font-size:14px}
.link{font-size:14px;text-decoration:underline;color:var(--text)}

/* section */
.section{position:absolute;left:22px;top:239px;width:1089px;height:353px;background:#fff;border:1px solid var(--line);border-radius:6px}
.section-tabs{position:absolute;left:0;top:0;width:100%;height:32px;display:flex;border-bottom:1px solid var(--line)}
.section-tabs span{height:32px;padding:0 16px;display:flex;align-items:center;font-size:15.5px;color:var(--text);border-right:1px solid var(--line)}
.section-tabs .active{box-shadow:inset 0 -2px 0 var(--blue-soft)}

.status{left:34px;top:828px;width:1133px;height:29px;background:var(--status);border:1px dashed var(--status-line);border-radius:5px;display:flex;align-items:center;justify-content:center;font-size:14.5px;color:var(--text)}
</style>
</head>
<body>

<header class="abs topbar">
  <div class="session">
    <span>Logged In As <b>Dana Whitfield</b>
      <svg width="12" height="12" viewBox="0 0 12 12"><circle cx="6" cy="6" r="5" fill="#9aa3ad"/><circle cx="6" cy="6" r="2" fill="#111419"/></svg></span>
    <span>Current Role <b>administrator</b>
      <svg width="10" height="7" viewBox="0 0 10 7" fill="none" stroke="#9aa3ad" stroke-width="1.6"><path d="m1 1 4 4 4-4"/></svg></span>
  </div>
  <nav class="utility"><span>Touch</span><span>New Tab</span><span>Help</span><span>Support</span><span>Log Out</span></nav>
</header>

<nav class="abs modules">
  <span>Home</span><span>eSource</span><span class="active">eBuy</span><span>eRequest</span><span>eSell</span><span>eStock</span><span>ePlan</span><span>Preferences</span>
</nav>
<div class="abs brand">Brightmoor</div>

<nav class="abs subnav">
  <span class="active">Orders</span><span>Receipes</span><span>Shipments</span><span>Invoices</span>
  <span class="divider"></span>
  <span>Priacing</span><span>Tables</span><span>Reports</span><span>Inquiries</span><span>Periodic Tasks</span><span>Workflows</span>
</nav>

<h1 class="abs page-title">Purchase Order Lines</h1>
<nav class="abs view-tabs">
  <span class="active">Header</span><span class="dot">Lines</span><span>Charges</span><span class="dot">Notes</span>
</nav>

<div class="abs toolbar">
  <span class="tool"><svg width="16" height="17" viewBox="0 0 16 17" fill="none" stroke="#fff" stroke-width="1.6"><path d="M11 5 5 11a2 2 0 0 0 3 3l7-7a3.5 3.5 0 0 0-5-5L3 9a5 5 0 0 0 7 7"/></svg></span>
  <span class="tool"><svg width="18" height="18" viewBox="0 0 18 18" fill="none" stroke="#fff" stroke-width="1.6"><rect x="1" y="1" width="11" height="14" rx="1.5"/><circle cx="10" cy="11" r="3.5"/><path d="m12.5 13.5 4 4"/></svg></span>
  <span class="tool"><svg width="20" height="16" viewBox="0 0 20 16" fill="#fff" stroke="#fff" stroke-width="1.4"><path d="M3 12 10 5l7 7" fill="none"/><circle cx="3" cy="12" r="2.5"/><circle cx="10" cy="5" r="2.5"/><circle cx="17" cy="12" r="2.5"/></svg></span>
  <span class="tool"><svg width="18" height="16" viewBox="0 0 18 16" fill="#fff"><rect x="0" y="4" width="18" height="12" rx="2"/><rect x="6" y="1" width="6" height="4" rx="1" fill="none" stroke="#fff" stroke-width="1.6"/></svg></span>
  <span class="tool"><svg width="17" height="17" viewBox="0 0 17 17"><circle cx="8.5" cy="8.5" r="8" fill="#7597c1"/><path d="M6.3 6.4a2.3 2.3 0 1 1 3.2 2.1c-.7.3-1 .7-1 1.4M8.5 12.2v.3" fill="none" stroke="#3d6fa8" stroke-width="1.5"/></svg></span>
  <span class="tool"><svg width="19" height="19" viewBox="0 0 20 20" stroke="#fff" stroke-width="2" fill="none"><path d="m3 17 9-9M14 2a4 4 0 0 0-2 6l2 2a4 4 0 0 0 5-3l-3 1-2-2 1-3zM3 3l5 5M12 12l5 5"/></svg>View GL Accounts</span>
  <span class="tool"><svg width="21" height="18" viewBox="0 0 21 18" fill="#fff"><rect x="0" y="2" width="15" height="12" rx="1.5"/><circle cx="15.5" cy="12.5" r="5" fill="#3d6fa8" stroke="#fff" stroke-width="1.5"/><path d="M15.5 9.5v6M12.5 12.5h6" stroke="#fff" stroke-width="1.5"/></svg>Post Order</span>
  <span class="spacer"></span>
  <span class="tool dim left-sep"><svg width="13" height="13" viewBox="0 0 13 13" fill="none" stroke="#fff" stroke-width="1.6"><circle cx="5" cy="5" r="4"/><path d="m8 8 4 4"/></svg>search</span>
  <span class="tool dim"><svg width="13" height="13" viewBox="0 0 13 13"><circle cx="6.5" cy="6.5" r="6" fill="#fff"/><path d="M6.5 3v7M3 6.5h7" stroke="#3d6fa8" stroke-width="1.6"/></svg>new</span>
  <span class="tool"><svg width="14" height="12" viewBox="0 0 14 12" fill="none" stroke="#fff" stroke-width="2"><path d="m1 6 4 4 8-9"/></svg>apply</span>
  <span class="tool"><svg width="13" height="13" viewBox="0 0 13 13"><circle cx="6.5" cy="6.5" r="6" fill="#fff"/><path d="m4 4 5 5M9 4 4 9" stroke="#3d6fa8" stroke-width="1.6"/></svg>delete</span>
  <span class="tool last"><svg width="14" height="12" viewBox="0 0 14 12" fill="none" stroke="#fff" stroke-width="2"><path d="M5 1 1 5l4 4M1 5h7a5 5 0 0 1 5 5"/></svg>back</span>
</div>

<main class="abs content"></main>

<section class="abs panel">
  <!-- order header -->
  <div class="row" style="left:7px;top:9px"><span class="label" style="width:140px;margin-right:6px">Order #</span><span>100159</span></div>
  <div class="row" style="left:292px;top:12px"><span class="order-type">Regular Purchase Order</span></div>
  <div class="row" style="left:896px;top:11px"><span class="hold">Hold For Completion</span></div>

  <div class="row" style="left:7px;top:39px"><span class="label" style="width:140px;margin-right:6px">Ship From</span>
    <span class="field" style="width:112px">1001</span><span style="margin:0 7px 0 9px">/</span><span class="field" style="width:25px">0</span></div>

  <div class="row" style="left:153px;top:70px"><span class="field" style="width:454px">Harborline Medical Goods</span></div>
  <div class="row" style="left:7px;top:96px"><span class="label" style="width:140px;margin-right:6px">Address</span><span class="field" style="width:454px">14 Tidewater Rd</span></div>
  <div class="row" style="left:153px;top:122px"><span class="field" style="width:454px"></span></div>

  <svg class="abs" style="left:629px;top:72px" width="25" height="25" viewBox="0 0 25 25" role="img" aria-label="Address verification"><circle cx="12.5" cy="12.5" r="12" fill="#dcb57d" stroke="#b78b50"/><circle cx="12.5" cy="12.5" r="5" fill="none" stroke="#94682f" stroke-width="1.5"/></svg>
  <div class="row" style="left:617px;top:124px"><span class="dpv">DPV Unconfirmed</span></div>
  <div class="row" style="left:622px;top:145px;gap:6px">
    <svg width="15" height="15" viewBox="0 0 15 15"><rect x=".5" y=".5" width="14" height="14" rx="3" fill="#fff" stroke="#8a94a1"/><path d="m3.5 7.5 3 3 5-6" fill="none" stroke="#1f2630" stroke-width="1.8"/></svg><span>Accept</span></div>

  <div class="row" style="left:7px;top:146px"><span class="label" style="width:140px;margin-right:6px">City</span><span class="field" style="width:307px">Saltcove</span></div>
  <div class="row" style="left:473px;top:146px"><span class="label" style="width:60px;margin-right:5px">State</span><span class="field" style="width:38px">MA</span></div>

  <div class="row" style="left:7px;top:172px"><span class="label" style="width:140px;margin-right:6px">Zip</span><span class="field" style="width:119px">01962-4410</span></div>
  <div class="row" style="left:281px;top:172px"><span class="label" style="width:80px;margin-right:5px">Country</span><span class="field" style="width:65px">US</span></div>
  <div class="row" style="left:508px;top:172px"><span class="link">Add Contact</span></div>

  <!-- shipping section -->
  <div class="section">
    <nav class="section-tabs">
      <span>Order Info</span><span class="active">Shipping</span><span>Payment</span><span>Accounts</span><span>Totals / Approval</span>
    </nav>

    <div class="row" style="left:0;top:58px"><span class="label" style="width:125px;margin-right:6px">Receive At</span><span class="select" style="width:127px">ALCH<i></i></span><span class="req">*</span></div>
    <div class="row" style="left:0;top:83px"><span class="label" style="width:125px;margin-right:6px">Carrier</span><span class="select" style="width:127px">Swiftline<i></i></span><span class="req">*</span></div>
    <div class="row" style="left:0;top:108px"><span class="label" style="width:125px;margin-right:6px">Express Service</span><span class="select" style="width:127px"><i></i></span></div>
    <div class="row" style="left:0;top:133px"><span class="label" style="width:125px;margin-right:6px">FOB</span><span class="select" style="width:127px"><i></i></span></div>
    <div class="row" style="left:0;top:158px"><span class="label" style="width:125px;margin-right:6px">Order Ship Rule</span><span class="select" style="width:158px">Partials<i></i></span><span class="req">*</span></div>
    <div class="row" style="left:0;top:184px"><span class="label" style="width:125px;margin-right:6px">Line Ship Rule</span><span class="select" style="width:158px">Partials<i></i></span><span class="req">*</span></div>

    <div class="row" style="left:331px;top:58px"><span class="label" style="width:160px;margin-right:5px">Request Date</span><span class="select" style="width:106px;padding-right:6px">01/07/2018</span>
      <svg style="margin-left:5px" width="18" height="18" viewBox="0 0 18 18"><rect x=".5" y="1.5" width="17" height="16" rx="2" fill="#fff" stroke="#6e9bd0"/><rect x=".5" y="1.5" width="17" height="4.5" rx="2" fill="#6e9bd0"/><path d="M4 9h2v2H4zM8 9h2v2H8zM12 9h2v2h-2zM4 13h2v2H4zM8 13h2v2H8z" fill="#e08a2a"/></svg></div>
    <div class="row" style="left:331px;top:83px"><span class="label" style="width:160px;margin-right:5px">Freight Terms</span><span class="select" style="width:127px">Collect<i></i></span></div>
    <div class="row" style="left:331px;top:108px"><span class="label" style="width:160px;margin-right:5px">Freight Calc</span><span class="select" style="width:174px"><i></i></span></div>

    <div class="row" style="left:716px;top:58px"><span class="label" style="width:114px;text-align:left;margin-right:4px">Customer Ship To</span>
      <span class="field" style="width:98px;height:22px;background:#f3f5f8;border-color:#eceff3"></span><span style="margin:0 4px">/</span>
      <span class="field" style="width:34px;height:22px;background:#f3f5f8;border-color:#eceff3"></span></div>

    <svg class="abs" style="left:1019px;top:276px" width="36" height="46" viewBox="0 0 36 46" role="img" aria-label="Record locked"><path d="M9 20v-7a9 9 0 0 1 18 0v7" fill="none" stroke="var(--lock)" stroke-width="4"/><rect x="1" y="19" width="34" height="26" rx="4" fill="var(--lock)"/><path d="M10 28h16M10 33h16M10 38h16" stroke="#dcc34e" stroke-width="1.5"/></svg>
  </div>
</section>

<footer class="abs status">Click Search, or enter property values and click Apply</footer>

</body>
</html>
```